Lucky Harbour Fun Casino Entertainment

Looking to update my business card and make it look more modern, stand out and eye catching.
We are are fun casino business in Australia (primarily Sydney). Blackjack and Roulette are our most popular games although we have pretty much every game available for hire that you would find in a real casino. The final design would need to be sleek and appeal to the more upmarket corporate sector.
We mainly cater for Corporate Events, Private Parties, Fundraising Events, Team Building, Poker Tournaments
I think I'd prefer the colour Black.

Target Market(s)

High-end Corporate

Industry/Entity Type

Events

Contact Information for Business Card

Rob Kendall
Director
1300 482 617
0433 728 591
info@luckyharbour.com.au
www.luckyharbour.com.au
Facebook & Instagram @luckyharbourevents (proper social icons preferred)

Colors
000000
0255a3

Requirements
Must have
• Front side:
• Logo
• Contact details
• 'Australia's #1 Fun Casino Specialists'
• Back:
• Logo
Nice to have
• Back:
• Corporate Events
• Private Parties
• Poker Tournaments
• Fundraising
• Props & Theming
• Photo Booth
• Horse Racing Events
• The Vegas Sign attached, maybe on the back of the card in the background...?

```html
<!DOCTYPE html>
<html lang="en">
<head>
<meta charset="utf-8">
<title>Lucky Harbour Fun Casino Entertainment – Business Cards</title>
<link href="https://fonts.googleapis.com/css2?family=Lato:wght@400;700&family=Bebas+Neue&display=swap" rel="stylesheet">
<style>
  :root {
    --backdrop: #7b7b7b;
    --card-top: #2b2b2b;
    --card-bottom: #0b0b0b;
    --accent: #f9ab1f;
    --text-light: #e2e2e2;
    --text-muted: #c9c9c9;
    --rule: #8a8a8a;
    --band-text: #1a1a1a;
  }
  * { margin: 0; padding: 0; box-sizing: border-box; }
  html, body { width: 1200px; height: 1200px; overflow: hidden; }
  body {
    background: var(--backdrop);
    font-family: "Lato", Arial, sans-serif;
    position: relative;
  }
  .card {
    position: absolute;
    top: 310px;
    height: 595px;
    background: linear-gradient(180deg, var(--card-top) 0%, #1a1a1a 45%, var(--card-bottom) 100%);
    box-shadow: 2px 3px 6px rgba(0,0,0,0.45);
    color: var(--text-light);
    text-align: center;
  }
  .card--front { left: 234px; width: 365px; }
  .card--back { left: 627px; width: 370px; }

  .brand {
    position: absolute;
    left: 0; right: 0;
    display: flex;
    flex-direction: column;
    align-items: center;
    gap: 18px;
  }
  .card--front .brand { top: 95px; }
  .card--back .brand { top: 85px; }
  .brand__disc {
    width: 96px; height: 96px;
    border-radius: 50%;
    background: var(--accent);
  }
  .brand__name {
    font-weight: 700;
    font-size: 34px;
    letter-spacing: 1px;
    color: var(--accent);
    line-height: 1;
  }

  .person { position: absolute; top: 313px; left: 0; right: 0; }
  .person__name {
    font-weight: 700;
    font-size: 24px;
    color: var(--accent);
    line-height: 1.1;
  }
  .person__role {
    font-size: 17px;
    color: var(--text-muted);
    line-height: 1.2;
  }

  .divider {
    position: absolute;
    left: 0; right: 0;
    display: flex;
    justify-content: center;
    align-items: center;
    gap: 4px;
  }
  .divider::before, .divider::after {
    content: "";
    width: 40px;
    height: 1px;
    background: var(--rule);
    margin: 0 4px;
  }
  .divider--contact { top: 375px; }
  .divider--social { top: 496px; }
  .divider--social::before, .divider--social::after { width: 60px; }

  .icon {
    width: 21px; height: 21px;
    border-radius: 50%;
    background: var(--accent);
    display: flex;
    align-items: center;
    justify-content: center;
  }
  .icon svg { width: 13px; height: 13px; }
  .icon--social { background: #4a6fa5; }

  .contact {
    position: absolute;
    top: 401px; left: 0; right: 0;
    list-style: none;
    font-size: 17px;
    line-height: 21.7px;
    color: var(--text-light);
  }
  .social-handle {
    position: absolute;
    top: 520px; left: 0; right: 0;
    font-size: 17px;
    color: var(--text-light);
  }

  .tagline-band {
    position: absolute;
    top: 311px; left: 0; right: 0;
    height: 56px;
    background: var(--accent);
    display: flex;
    align-items: center;
    justify-content: center;
    font-family: "Bebas Neue", "Oswald", sans-serif;
    font-size: 27px;
    color: var(--band-text);
    letter-spacing: 0.2px;
  }
  .services {
    position: absolute;
    top: 400px; left: 0; right: 0;
    list-style: none;
    font-size: 17px;
    line-height: 21.5px;
    color: #ffffff;
    text-transform: uppercase;
  }
</style>
</head>
<body>

<section class="card card--front" aria-label="Business card front">
  <div class="brand">
    <div class="brand__disc"></div>
    <div class="brand__name">LUCKY HARBOUR</div>
  </div>

  <div class="person">
    <div class="person__name">ROB KENDALL</div>
    <div class="person__role">Director</div>
  </div>

  <div class="divider divider--contact">
    <span class="icon" aria-label="Phone">
      <svg viewBox="0 0 16 16"><path d="M3 2h3l1 3-2 1c1 2 2 3 4 4l1-2 3 1v3c0 1-1 2-2 2C6 14 2 10 2 4c0-1 0-2 1-2z" fill="#1a1a1a"/></svg>
    </span>
    <span class="icon" aria-label="Mobile">
      <svg viewBox="0 0 16 16"><rect x="4" y="1" width="8" height="14" rx="1.5" fill="none" stroke="#1a1a1a" stroke-width="1.8"/><circle cx="8" cy="12.5" r="1" fill="#1a1a1a"/></svg>
    </span>
    <span class="icon" aria-label="Email">
      <svg viewBox="0 0 16 16"><rect x="1.5" y="3.5" width="13" height="9" fill="none" stroke="#1a1a1a" stroke-width="1.6"/><path d="M1.5 3.5l6.5 5 6.5-5" fill="none" stroke="#1a1a1a" stroke-width="1.6"/></svg>
    </span>
    <span class="icon" aria-label="Website">
      <svg viewBox="0 0 16 16"><circle cx="8" cy="8" r="6.3" fill="none" stroke="#1a1a1a" stroke-width="1.6"/><path d="M1.7 8h12.6M8 1.7c-3 3.5-3 9 0 12.6M8 1.7c3 3.5 3 9 0 12.6" fill="none" stroke="#1a1a1a" stroke-width="1.3"/></svg>
    </span>
  </div>

  <ul class="contact">
    <li>1300 482 617</li>
    <li>0433 728 591</li>
    <li>info@luckyharbour.com.au</li>
    <li>www.luckyharbour.com.au</li>
  </ul>

  <div class="divider divider--social">
    <span class="icon icon--social" aria-label="Social profile"></span>
    <span class="icon icon--social" aria-label="Social profile"></span>
  </div>

  <div class="social-handle">@luckyharbourevents</div>
</section>

<section class="card card--back" aria-label="Business card back">
  <div class="brand">
    <div class="brand__disc"></div>
    <div class="brand__name">LUCKY HARBOUR</div>
  </div>

  <div class="tagline-band">AUSTRALIA'S #1 FUN CASINO SPECIALISTS</div>

  <ul class="services">
    <li>Corporate Events</li>
    <li>Private Parties</li>
    <li>Poker Tournaments</li>
    <li>Fundraising</li>
    <li>Props &amp; Theming</li>
    <li>Photo Booth</li>
    <li>Horse Racing Events</li>
  </ul>
</section>

</body>
</html>
```